business card deign

Logo needs the following on it.
1. attached logo
2. Tagline - "If it keeps a drink cold or the party going...we do it!"
3. Name- Dalton Pikes, Founder and CPO
4. Address - 412 E. Carver Avenue, Ste 2207, Tampa, FL. 33917
5. Phone - 555.318.4726

```html
<!DOCTYPE html>
<html lang="en">
<head>
<meta charset="utf-8">
<title>Kelvaro Business Card</title>
<link href="https://fonts.googleapis.com/css2?family=Roboto:wght@400;700&display=swap" rel="stylesheet">
<style>
  :root {
    --stage: #232323;
    --card: #171717;
    --card-edge: #0c0c0c;
    --ink: #ffffff;
    --ink-soft: #e6e6e6;
    --panel-light: #ffffff;
    --panel-mid: #d9d9d9;
  }
  * { margin: 0; padding: 0; box-sizing: border-box; }
  html, body { width: 1200px; height: 711px; overflow: hidden; }
  body {
    background: var(--stage);
    font-family: "Roboto", Arial, sans-serif;
    color: var(--ink);
    position: relative;
  }
  .card {
    position: absolute;
    width: 540px;
    height: 309px;
    border-radius: 22px;
    background: var(--card);
    box-shadow: 0 6px 0 var(--card-edge), 0 18px 34px rgba(0,0,0,.55);
    overflow: hidden;
  }
  .card-front { left: 40px; top: 201px; }
  .card-back { left: 620px; top: 201px; }

  .front-brand {
    position: absolute;
    inset: 0;
    display: flex;
    align-items: center;
    justify-content: center;
    gap: 18px;
  }
  .brand-dot {
    width: 22px; height: 22px;
    border-radius: 50%;
    background: var(--ink);
  }
  .brand-name {
    font-weight: 700;
    font-size: 44px;
    letter-spacing: 14px;
    color: var(--ink);
  }

  .back-details {
    position: absolute;
    left: 34px;
    top: 34px;
    width: 270px;
  }
  .back-brand {
    display: flex;
    align-items: center;
    gap: 10px;
    margin-bottom: 26px;
  }
  .back-brand .brand-dot { width: 12px; height: 12px; }
  .back-brand .brand-name { font-size: 20px; letter-spacing: 7px; }
  .identity {
    position: relative;
    padding-left: 20px;
    margin-bottom: 12px;
  }
  .identity::before {
    content: "";
    position: absolute;
    left: 0; top: 4px;
    width: 9px; height: 44px;
    background: var(--ink);
  }
  .person-name { font-weight: 700; font-size: 24px; line-height: 1.15; }
  .person-role { font-size: 14px; color: var(--ink-soft); margin-top: 2px; }
  .tagline {
    padding-left: 20px;
    font-size: 12px;
    line-height: 1.45;
    color: var(--ink-soft);
    margin-bottom: 14px;
  }
  .contact { list-style: none; padding-left: 20px; font-size: 12px; color: var(--ink-soft); }
  .contact li { display: flex; gap: 8px; align-items: flex-start; line-height: 1.45; margin-bottom: 4px; }
  .contact svg { flex: 0 0 12px; margin-top: 3px; }

  .back-artwork {
    position: absolute;
    right: 0; top: 0;
    width: 220px; height: 309px;
    background: linear-gradient(160deg, var(--panel-light) 0%, var(--panel-mid) 100%);
    border-top-left-radius: 120px 309px;
  }
</style>
</head>
<body>
  <section class="card card-front">
    <div class="front-brand">
      <span class="brand-dot"></span>
      <span class="brand-name">KELVARO</span>
    </div>
  </section>

  <section class="card card-back">
    <div class="back-details">
      <div class="back-brand">
        <span class="brand-dot"></span>
        <span class="brand-name">KELVARO</span>
      </div>
      <div class="identity">
        <div class="person-name">Dalton Pikes</div>
        <div class="person-role">Founder and CPO</div>
      </div>
      <p class="tagline">If it keeps a drink cold or<br>the party going...we do it!</p>
      <ul class="contact">
        <li>
          <svg width="12" height="12" viewBox="0 0 24 24" aria-hidden="true"><path fill="#fff" d="M6.6 10.8a15.1 15.1 0 0 0 6.6 6.6l2.2-2.2a1 1 0 0 1 1-.25 11.4 11.4 0 0 0 3.6.57 1 1 0 0 1 1 1V20a1 1 0 0 1-1 1A17 17 0 0 1 3 4a1 1 0 0 1 1-1h3.5a1 1 0 0 1 1 1c0 1.25.2 2.46.57 3.6a1 1 0 0 1-.25 1z"/></svg>
          <span>555.318.4726</span>
        </li>
        <li>
          <svg width="12" height="12" viewBox="0 0 24 24" aria-hidden="true"><path fill="none" stroke="#fff" stroke-width="2.4" d="M12 22s7-7.2 7-12.5A7 7 0 0 0 5 9.5C5 14.8 12 22 12 22z"/><circle cx="12" cy="9.5" r="2.5" fill="#fff"/></svg>
          <span>412 E. Carver Avenue, Ste 2207,<br>Tampa, FL. 33917</span>
        </li>
      </ul>
    </div>
    <div class="back-artwork" role="img" aria-label="Large black brand animal silhouette on a white field"></div>
  </section>
</body>
</html>
```